Lantern Hollow Brewing Company New Website with Food Ordering

We need a wordpress-based website for a local brewery & pizza kitchen. The final design will have 6 primary pages: home page, order pizza, our beers, visit us, about us, merch store. The website must integrate with tillpoint for kitchens for online ordering for takeout and delivery. It will also a feature a selection of beers and help customers navigate to the brewery and find hours of operation. The existing website is lanternhollowbrew.example. This is a very old website.

Industry/Entity Type

Brewery and food service

Coding

Coded - Design and coding required

Number of Pages Required

5+ page

Font styles to use
Sans Serif

Requirements
Must have
• ability to integrate seamlessly with tillpoint for kitchens, 21+ age gate
Nice to have
• see attached pdf

```html
<!DOCTYPE html>
<html lang="en">
<head>
<meta charset="utf-8">
<title>Lantern Hollow Brew – Square Pizza and Great Beer</title>
<link rel="stylesheet" href="https://fonts.googleapis.com/css2?family=Poppins:ital,wght@0,400;0,500;0,600;0,700;1,700&display=swap">
<style>
:root{
  --red:#9b1f24;
  --red-deep:#7e171b;
  --yellow:#fbb614;
  --gold:#ffc20e;
  --orange:#fb8c0b;
  --white:#ffffff;
  --frame:#ececec;
}
*{margin:0;padding:0;box-sizing:border-box}
html,body{width:682px;height:1200px;overflow:hidden}
body{font-family:"Poppins",sans-serif;background:var(--white);position:relative}
.abs{position:absolute}
.hero{position:absolute;left:0;top:0;width:682px;height:419px;
  background:radial-gradient(ellipse at 35% 45%,#a82a2e 0%,var(--red) 55%,var(--red-deep) 100%);overflow:hidden}
.brand-tile{left:77px;top:0;width:79px;height:71px;background:var(--white);border-radius:0 0 12px 12px;
  display:flex;align-items:center;justify-content:center;text-align:center;font-weight:700;font-size:9px;line-height:1.15;color:var(--red)}
.main-nav{left:196px;top:29px;width:321px;height:27px;background:var(--gold);border-radius:14px;
  display:flex;align-items:center;justify-content:center;gap:14px;font-size:9px;font-weight:600;color:var(--red)}
.promo-burst{left:536px;top:17px;width:112px;height:54px}
.hero-photo{left:376px;top:0;width:306px;height:345px}
.chevron{left:46px;top:113px;width:56px;height:56px}
.headline{left:111px;top:104px;font-size:30px;font-weight:700;line-height:38px;color:var(--white)}
.headline em{font-style:normal;color:var(--gold)}
.location{left:113px;top:185px;font-size:16.5px;font-weight:600;color:var(--gold);display:flex;align-items:center;gap:6px}
.hero-copy{left:114px;top:220px;width:243px;font-size:9.2px;font-weight:500;line-height:18.5px;color:var(--white);text-align:justify}
.btn{position:absolute;height:20px;border-radius:10px;display:flex;align-items:center;justify-content:center;font-size:8.5px;font-weight:600}
.btn-outline{background:var(--white);color:var(--red);border:2px solid var(--gold);font-weight:500}
.btn-fill{background:var(--orange);color:var(--white)}
.order{position:absolute;left:0;top:419px;width:682px;height:322px;background:var(--yellow);overflow:hidden}
.photo{position:absolute;border:9px solid var(--frame);border-radius:26px}
.order-title{left:0;width:782px;top:40px;text-align:center;font-size:21px;font-weight:700;color:var(--red);letter-spacing:.5px}
.order-copy{left:250px;top:77px;width:282px;text-align:center;font-size:7.4px;font-weight:500;line-height:13px;color:var(--red)}
.order-list{left:335px;top:121px;list-style:none}
.order-list li{display:flex;align-items:center;gap:10px;height:39.5px;font-size:12px;color:var(--red)}
.order-list .ico{width:31px;height:31px;border-radius:50%;background:var(--red);display:flex;align-items:center;justify-content:center}
.story{position:absolute;left:0;top:741px;width:682px;height:271px;background:var(--red)}
.story h2{position:absolute;left:0;width:682px;top:31px;text-align:center;font-size:21px;font-weight:700;color:var(--white)}
.story p{position:absolute;left:148px;top:75px;width:386px;text-align:center;font-size:11.6px;line-height:21.5px;color:var(--gold)}
.btn-lg{height:27px;border-radius:12px;font-size:10.5px;font-weight:500}
.btn-gold{background:var(--gold);color:var(--red)}
.btn-white{background:var(--white);color:var(--red)}
.footer{position:absolute;left:0;top:1012px;width:682px;height:158px;background:var(--yellow)}
.footer-brand{left:90px;top:45px;width:105px;font-size:16px;font-weight:700;line-height:19px;color:var(--red);display:flex;align-items:center;gap:8px}
.footer-brand .mark{width:14px;height:14px;background:var(--red);flex:none}
.footer h3{position:absolute;font-size:8.5px;font-weight:600;color:var(--red);letter-spacing:.3px}
.footer-copy{left:233px;top:39px;width:198px;font-size:7.3px;font-weight:500;line-height:16px;color:var(--red);text-align:justify}
.contact{left:468px;top:37px;list-style:none}
.contact li{display:flex;align-items:center;gap:8px;height:18px;font-size:7.4px;color:var(--red)}
.legal{position:absolute;left:63px;top:1181px;font-size:6.6px;color:var(--red)}
</style>
</head>
<body>

<header class="hero">
  <div class="abs brand-tile">Lantern<br>Hollow<br>Brew</div>
  <nav class="abs main-nav">
    <span>The Kitchen</span><span>Our Beers</span><span>Visit Us</span><span>About Us</span><span>Merch</span>
  </nav>

  <svg class="abs hero-photo" viewBox="0 0 306 345" role="img" aria-label="Photo of a square pepperoni pizza on a cooling rack beside a beer glass">
    <defs>
      <linearGradient id="pizzaTone" x1="0" y1="0" x2="1" y2="1">
        <stop offset="0" stop-color="#d9c2b4"/>
        <stop offset=".45" stop-color="#b8403a"/>
        <stop offset="1" stop-color="#8c8f96"/>
      </linearGradient>
    </defs>
    <path d="M150 0 H306 V250 L240 310 C200 345 110 350 60 320 C5 285 -5 200 20 140 Z" fill="url(#pizzaTone)"/>
    <path d="M22 178 C5 250 40 320 110 338 C170 352 215 335 255 300 L306 258" fill="none" stroke="var(--gold)" stroke-width="5"/>
  </svg>

  <svg class="abs promo-burst" viewBox="0 0 112 54" aria-hidden="false">
    <polygon points="56,0 64,9 78,3 80,14 98,10 94,21 112,25 97,31 106,42 89,41 86,53 72,46 60,54 51,45 37,52 33,42 16,45 20,34 2,30 17,24 8,13 26,15 28,4 43,9" fill="var(--gold)" stroke="var(--white)" stroke-width="2"/>
    <text x="56" y="31" text-anchor="middle" font-family="Poppins, sans-serif" font-size="12" font-weight="700" fill="var(--red)">Try Ember!</text>
  </svg>

  <svg class="abs chevron" viewBox="0 0 56 56" aria-hidden="true">
    <circle cx="2" cy="2" r="1" fill="var(--gold)"/><circle cx="7" cy="2" r="1" fill="var(--gold)"/><circle cx="12" cy="2" r="1" fill="var(--gold)"/>
    <polygon points="0,8 18,8 44,28 18,48 0,48 26,28" fill="var(--orange)"/>
    <polygon points="6,8 24,8 44,28 24,48 6,48 26,28" fill="var(--gold)"/>
    <circle cx="42" cy="54" r="1" fill="var(--gold)"/><circle cx="47" cy="54" r="1" fill="var(--gold)"/><circle cx="52" cy="54" r="1" fill="var(--gold)"/>
  </svg>

  <h1 class="abs headline">Square <em>Pizza</em><br>And Great <em>Beer</em></h1>
  <div class="abs location">In Portland, Maine
    <svg width="12" height="15" viewBox="0 0 12 15" aria-hidden="true"><path d="M6 1C3.2 1 1 3.2 1 6c0 3.6 5 8 5 8s5-4.4 5-8c0-2.8-2.2-5-5-5z" fill="none" stroke="var(--gold)" stroke-width="2"/><circle cx="6" cy="6" r="1.6" fill="var(--gold)"/></svg>
  </div>
  <p class="abs hero-copy">Lorem Ipsum is simply dummy text of the printing and typesetting industry. Lorem Ipsum has been the industry's standard dummy text ever since the 1500s.</p>

  <a class="btn btn-outline" style="left:72px;top:350px;width:78px;height:21px">ORDER PIZZA</a>
  <a class="btn btn-fill" style="left:164px;top:351px;width:77px">VISIT US</a>
  <a class="btn btn-fill" style="left:255px;top:351px;width:77px">OUR BEERS</a>
  <a class="btn btn-fill" style="left:347px;top:351px;width:77px">ABOUT US</a>
</header>

<section class="order">
  <div class="photo" role="img" aria-label="Photo of a Detroit-style pizza with tomato and basil" style="left:-40px;top:-10px;width:250px;height:230px;transform:rotate(-22deg);background:linear-gradient(135deg,#3b3431,#d89c48 45%,#b8442f)"></div>
  <div class="photo" role="img" aria-label="Photo of pizza and beer on a red table" style="left:-10px;top:192px;width:160px;height:145px;transform:rotate(-3deg);background:linear-gradient(135deg,#c9bfb6,#a8332e 50%,#6e2523)"></div>
  <div class="photo" role="img" aria-label="Photo of square pizzas in a kitchen display" style="left:133px;top:160px;width:145px;height:128px;transform:rotate(6deg);background:linear-gradient(160deg,#4a5f6a,#c8813f 55%,#e0b57a)"></div>
  <div class="photo" role="img" aria-label="Photo of a mushroom and olive square pizza" style="left:553px;top:36px;width:135px;height:115px;transform:rotate(5deg);background:linear-gradient(135deg,#c9a07c,#a63a2e 55%,#7a3b2c)"></div>
  <div class="photo" role="img" aria-label="Photo of hands sharing slices of pizza" style="left:560px;top:160px;width:135px;height:128px;transform:rotate(-3deg);background:linear-gradient(135deg,#5a4c46,#cf7a3c 55%,#d9c6b6)"></div>

  <h2 class="abs order-title">ORDER PIZZA</h2>
  <p class="abs order-copy">Lorem Ipsum is simply dummy text of the printing and typesetting industry. Lorem Ipsum has been the industry's standard dummy text.</p>
  <ul class="abs order-list">
    <li><span class="ico"><svg width="16" height="16" viewBox="0 0 16 16"><rect x="2" y="1" width="10" height="13" fill="none" stroke="#fff" stroke-width="1.3"/><circle cx="7" cy="7" r="3" fill="none" stroke="#fff" stroke-width="1.3"/><path d="M9 9l5 5" stroke="#fff" stroke-width="1.5"/></svg></span>View menu</li>
    <li><span class="ico"><svg width="16" height="16" viewBox="0 0 16 16"><path d="M1 3h2l2 8h8l2-6H4" fill="none" stroke="#fff" stroke-width="1.3"/><circle cx="6" cy="14" r="1.2" fill="#fff"/><circle cx="12" cy="14" r="1.2" fill="#fff"/></svg></span>Order carryout</li>
    <li><span class="ico"><svg width="18" height="14" viewBox="0 0 18 14"><rect x="1" y="3" width="10" height="7" fill="none" stroke="#fff" stroke-width="1.3"/><path d="M11 5h4l2 3v2h-6" fill="none" stroke="#fff" stroke-width="1.3"/><circle cx="5" cy="12" r="1.4" fill="#fff"/><circle cx="14" cy="12" r="1.4" fill="#fff"/></svg></span>Order delivery</li>
    <li><span class="ico"><svg width="16" height="16" viewBox="0 0 16 16"><path d="M3 2l3 0 1 4-2 1c1 2 2 3 4 4l1-2 4 1v3c-6 1-12-5-11-11z" fill="none" stroke="#fff" stroke-width="1.3"/></svg></span>Questions? Give us a call</li>
  </ul>
</section>

<section class="story">
  <h2>What is Detroit-style pizza?</h2>
  <p>Lorem Ipsum is simply dummy text of the printing and typesetting industry. Lorem Ipsum has been the industry's standard dummy text ever since the 1500s, when an unknown printer took a galley of type and scrambled it to make a type specimen book. It has survived not only five centuries, but also the leap into electronic typesetting.</p>
  <a class="btn btn-lg btn-gold" style="left:214px;top:207px;width:122px">ORDER ONLINE</a>
  <a class="btn btn-lg btn-white" style="left:355px;top:207px;width:122px">VIEW FULL MENU</a>
</section>

<footer class="footer">
  <div class="abs footer-brand"><span class="mark"></span>Lantern Hollow Brew</div>
  <h3 style="left:233px;top:22px">LANTERN HOLLOW BREW</h3>
  <p class="abs footer-copy">Lorem Ipsum is simply dummy text of the printing and typesetting industry. Lorem Ipsum has been the industry's standard dummy text ever since the 1500s, when an unknown printer took a galley of type and scrambled it to make a type specimen book. It has survived not only five centuries</p>
  <h3 style="left:484px;top:22px">CONTACT US</h3>
  <ul class="abs contact">
    <li><svg width="8" height="8" viewBox="0 0 16 16"><path d="M3 1h4l1 4-2 1c1 2 2 4 4 4l1-2 4 1v4C8 14 2 8 3 1z" fill="var(--red)"/></svg>0100555000</li>
    <li><svg width="8" height="8" viewBox="0 0 16 12"><rect x="1" y="1" width="14" height="10" fill="var(--red)"/><path d="M1 1l7 6 7-6" fill="none" stroke="var(--yellow)" stroke-width="1.3"/></svg>hello@lanternhollowbrew.example</li>
    <li><svg width="8" height="9" viewBox="0 0 12 15"><path d="M6 1C3.2 1 1 3.2 1 6c0 3.6 5 8 5 8s5-4.4 5-8c0-2.8-2.2-5-5-5z" fill="var(--red)"/><circle cx="6" cy="6" r="1.8" fill="var(--yellow)"/></svg>42 Harbor Lane, Portland, ME</li>
  </ul>
</footer>

<p class="legal">© COPYRIGHTS 2022 LANTERN HOLLOW BREW | ALL RIGHTS RESERVED</p>

</body>
</html>
```